Tech business card design

We need an amazing business card design for our new business 'Pexla' a marketing tech startup based in Sydney, Australia. We provide an online marketplace for businesses to search and buy advertising media, connect with service providers and learn more about marketing. We wish to communicate 'cool tech', reliability and professionalism and design based around our logo.

Target Market(s)

Business Owners

Contact Information for Business Card

Name
Position
Email Address
Website
Phone Number

Font styles to use
Other font styles liked:
• Avenir & Avenir Next

Colors

Designer to choose colors to be used in the design.

```html
<!DOCTYPE html>
<html lang="en">
<head>
<meta charset="utf-8">
<title>Pexla Business Card</title>
<link href="https://fonts.googleapis.com/css2?family=Nunito+Sans:wght@400;600;800&display=swap" rel="stylesheet">
<style>
  :root {
    --navy: #16185a;
    --navy-light: #3a3d82;
    --paper: #f7f7f8;
    --ink: #22245e;
    --ink-soft: #4a4c80;
    --backdrop: #d9d6d0;
    --white: #ffffff;
  }
  * { margin: 0; padding: 0; box-sizing: border-box; }
  html, body {
    width: 1200px; height: 780px; overflow: hidden;
    background: var(--backdrop);
    font-family: "Nunito Sans", "Avenir Next", Avenir, sans-serif;
  }
  .stage { width: 1200px; height: 780px; display: flex; align-items: center; justify-content: center; }
  .card {
    position: relative; width: 1000px; height: 572px;
    background: var(--navy);
    box-shadow: 0 18px 40px rgba(0,0,0,.25);
    overflow: hidden;
  }
  .card-shape { position: absolute; inset: 0; }
  .brand-name {
    position: absolute; top: 60px; left: 250px; width: 480px;
    text-align: center;
    font-size: 140px; font-weight: 800; letter-spacing: -4px;
    color: var(--ink); line-height: 1;
  }
  .contact { position: absolute; left: 160px; top: 300px; color: var(--ink); }
  .contact-name { font-size: 28px; font-weight: 800; line-height: 1.1; }
  .contact-role { font-size: 18px; font-weight: 600; margin-bottom: 18px; }
  .contact-address { font-size: 18px; line-height: 1.3; color: var(--ink-soft); margin-bottom: 16px; }
  .contact-line { display: flex; align-items: center; gap: 10px; font-size: 18px; line-height: 1.35; color: var(--ink-soft); }
  .contact-icon { width: 20px; height: 20px; flex: none; }
  .website {
    position: absolute; right: 24px; bottom: 62px;
    color: var(--white); font-size: 18px; font-weight: 600; letter-spacing: 1px;
  }
</style>
</head>
<body>
<main class="stage">
  <section class="card" aria-label="Pexla business card">
    <svg class="card-shape" viewBox="0 0 1000 572" aria-hidden="true">
      <path d="M300,0 L740,0 Q870,250 760,536 L90,536 Q0,280 300,0 Z" fill="var(--paper)"/>
      <rect x="0" y="536" width="1000" height="14" fill="var(--navy-light)"/>
    </svg>

    <div class="brand-name">pexla</div>

    <div class="contact">
      <p class="contact-name">Mara Linden</p>
      <p class="contact-role">Manager</p>
      <p class="contact-address">PO Box 418, Harbour Lane<br>3rd Street Sydney<br>Australia</p>
      <p class="contact-line">
        <svg class="contact-icon" viewBox="0 0 22 22" aria-hidden="true">
          <circle cx="11" cy="11" r="10" fill="var(--ink-soft)"/>
          <path d="M7.5,6 L9.5,6 L10.3,8.6 L9.1,9.6 Q10,12 12.4,13 L13.4,11.8 L16,12.6 L16,14.6 Q10,16 7.5,6 Z" fill="#fff"/>
        </svg>
        555.201.7734
      </p>
      <p class="contact-line">
        <svg class="contact-icon" viewBox="0 0 22 22" aria-hidden="true">
          <circle cx="11" cy="11" r="10" fill="var(--ink-soft)"/>
          <rect x="6" y="7.5" width="10" height="7" fill="#fff"/>
          <path d="M6,7.5 L11,11.5 L16,7.5" fill="none" stroke="var(--ink-soft)" stroke-width="1"/>
        </svg>
        hello@pexlamail.com
      </p>
    </div>

    <p class="website">www.pexlaweb.com</p>
  </section>
</main>
</body>
</html>
```